Accountability Project Graphics

I want to create 10 social media graphics (new Instagram size 4:5 (1080 x 1350 pixels) focusing on our Quilvo Accountability App, using any of the 3 pictures attached. Use the attached pics only, NO RANDOM STOCK PHOTOGRAPHY. For the color scheme, use the landing page colors/fonts (attached).
You can add any of the 3 photos attached but I mainly need BOLD text that includes these headlines and sub-headlines on them.
Please NOTE for all the headlines below, also add this sub-headline on each graphic:
Stay Consistent with RT in Your Pocket!
Here are the headlines:
• Stop Starting Over Every Monday
• You don't need more willpower. You need more support
• Built for women who are tired of doing this alone
• When Motivation Fades, RT Checks In
• The Support System You've Been Missing
• Support When Motivation Disappears
• What if RT Checked in Every Day?
• The Missing Piece Isn't Another Diet
• Eat the food you love. Stay accountable every day.
• One Bad Meal Doesn't Mean You Failed
women over 40 trying to lose weight

```html
<!DOCTYPE html>
<html lang="en">
<head>
<meta charset="utf-8">
<title>Accountability App Social Graphics</title>
<link rel="stylesheet" href="https://fonts.googleapis.com/css2?family=Merriweather:ital,wght@0,900;1,900&family=Outfit:wght@600&display=swap">
<style>
:root{
  --board:#a7a7a7;
  --plum:#2e1b3d;
  --rose:#c9587b;
  --hot:#e0527f;
  --blush:#f8d3e3;
  --white:#ffffff;
}
*{margin:0;padding:0;box-sizing:border-box}
html,body{width:1200px;height:2957px;overflow:hidden;background:var(--board)}
.board{position:relative;width:1200px;height:2957px}
.tile{position:absolute;width:431px;height:538px;overflow:hidden;background:var(--white)}
.tile.dark{background:var(--plum)}
.tile svg.art{position:absolute;inset:0;width:431px;height:538px}
.col-l{left:156px}.col-r{left:612px}
.row-1{top:79px}.row-2{top:645px}.row-3{top:1210px}.row-4{top:1775px}.row-5{top:2340px}
.headline{position:absolute;font-family:"Merriweather",Georgia,serif;font-weight:900;line-height:1.08;color:var(--plum)}
.headline em{font-style:italic}
.sub{position:absolute;font-family:"Outfit",Arial,sans-serif;font-weight:600;line-height:1.18;color:var(--plum)}
.pink{color:var(--rose)}
.hot{color:var(--hot)}
.light{color:var(--white)}
.right{text-align:right}
.center{text-align:center}
</style>
</head>
<body>
<main class="board">
<svg width="0" height="0" style="position:absolute">
  <defs>
    <linearGradient id="photoTone" x1="0" y1="0" x2="1" y2="1">
      <stop offset="0" stop-color="#b79aa8"/><stop offset="1" stop-color="#3b2f46"/>
    </linearGradient>
    <linearGradient id="photoWarm" x1="0" y1="0" x2="1" y2="1">
      <stop offset="0" stop-color="#d9c1c9"/><stop offset="1" stop-color="#6a4a63"/>
    </linearGradient>
  </defs>
</svg>

<section class="tile col-l row-1">
  <svg class="art" viewBox="0 0 431 538">
    <rect width="431" height="212" fill="var(--rose)"/>
    <circle cx="371" cy="335" r="190" fill="var(--rose)"/>
    <circle cx="395" cy="335" r="175" fill="var(--blush)"/>
    <path role="img" aria-label="Photo of the coach in a black lace top, hand on hip" d="M300 120 Q340 95 370 130 L400 220 Q420 330 400 538 L270 538 Q255 420 250 330 Q260 210 300 120Z" fill="url(#photoTone)"/>
  </svg>
  <h2 class="headline light" style="left:26px;top:30px;font-size:47px">Stop Starting<br><span style="font-size:42px">Over <em>Every</em></span><br><em style="font-size:46px">Monday</em></h2>
  <p class="sub" style="left:26px;top:232px;font-size:23px">Stay<br>Consistent<br>with<br><span class="pink" style="font-size:29px">RT in Your<br>Pocket!</span></p>
</section>

<section class="tile dark col-r row-1">
  <svg class="art" viewBox="0 0 431 538">
    <path d="M431 255 Q330 260 250 330 Q170 410 60 370 Q20 360 0 380 L0 538 L431 538Z" fill="var(--white)"/>
    <circle role="img" aria-label="Photo of two women hugging and laughing" cx="205" cy="450" r="160" fill="url(#photoWarm)"/>
  </svg>
  <h2 class="headline light center" style="left:0;width:431px;top:22px;font-size:39px;line-height:1.14">You don't need<br>more willpower.<br><em>You need<br>more support</em></h2>
  <p class="sub light center" style="left:0;width:431px;top:215px;font-size:20px">Stay Consistent with<br><span class="hot" style="font-size:26px">RT in Your Pocket!</span></p>
</section>

<section class="tile dark col-l row-2">
  <svg class="art" viewBox="0 0 431 538">
    <circle cx="80" cy="480" r="280" fill="var(--hot)"/>
    <circle role="img" aria-label="Photo of the coach standing with a smiling client" cx="60" cy="480" r="280" fill="url(#photoWarm)"/>
  </svg>
  <h2 class="headline light" style="left:24px;top:38px;font-size:41px;line-height:1.2">Built for women<br><em class="hot">who are tired of</em><br><em>doing this alone</em></h2>
  <p class="sub light right" style="right:28px;top:202px;font-size:22px">Stay Consistent<br>with <span class="hot">RT in Your</span><br><span class="hot">Pocket!</span></p>
</section>

<section class="tile col-r row-2">
  <svg class="art" viewBox="0 0 431 538">
    <circle cx="395" cy="326" r="150" fill="var(--rose)"/>
    <circle cx="26" cy="470" r="272" fill="var(--plum)"/>
    <circle role="img" aria-label="Photo of the coach smiling in a games room" cx="8" cy="470" r="272" fill="url(#photoTone)"/>
  </svg>
  <h2 class="headline" style="left:28px;top:28px;font-size:38px;line-height:1.15">When Motivation<br><span style="font-size:52px">Fades,</span><br><span class="pink" style="font-size:42px">RT Checks In</span></h2>
  <p class="sub light" style="left:300px;top:242px;font-size:24px">Stay<br>Consistent<br>with <span style="font-size:28px">RT in</span><br><span style="font-size:30px">Your<br>Pocket!</span></p>
</section>

<section class="tile col-l row-3">
  <svg class="art" viewBox="0 0 431 538">
    <circle cx="300" cy="50" r="165" fill="var(--plum)"/>
    <path d="M0 150 Q0 135 60 135 L230 135 Q410 135 410 335 Q410 505 230 505 L0 505Z" fill="var(--rose)"/>
    <circle role="img" aria-label="Photo of two women hugging and laughing" cx="305" cy="82" r="140" fill="url(#photoWarm)"/>
  </svg>
  <h2 class="headline light" style="left:26px;top:165px;font-size:45px;line-height:1.15">The<br>Support<br>System You've<br>Been Missing</h2>
  <p class="sub light" style="left:26px;top:412px;font-size:25px">Stay Consistent with<br>RT in Your Pocket!</p>
</section>

<section class="tile dark col-r row-3">
  <svg class="art" viewBox="0 0 431 538">
    <circle cx="295" cy="50" r="150" fill="var(--hot)"/>
    <circle cx="-20" cy="450" r="85" fill="var(--white)"/>
    <path role="img" aria-label="Photo of the coach in a black outfit, hand on hip" d="M300 40 Q340 30 355 75 L400 150 Q431 200 431 300 L431 538 L270 538 Q270 420 250 340 Q230 250 260 170 Q270 70 300 40Z" fill="url(#photoTone)"/>
  </svg>
  <h2 class="headline light" style="left:24px;top:128px;font-size:37px;line-height:1.2">Support<br>When<br><em>Motivation<br>Disappears</em></h2>
  <p class="sub light" style="left:94px;top:345px;font-size:23px"><span class="hot">Stay<br>Consistent<br>with</span><br><span style="font-size:28px">RT in Your<br>Pocket!</span></p>
</section>

<section class="tile col-l row-4">
  <svg class="art" viewBox="0 0 431 538">
    <path d="M0 0 L431 0 L431 180 Q300 180 240 230 Q170 300 60 250 L0 240Z" fill="var(--plum)"/>
    <circle cx="5" cy="540" r="130" fill="var(--plum)"/>
    <circle role="img" aria-label="Photo of the coach smiling in a games room" cx="120" cy="75" r="178" fill="url(#photoTone)"/>
  </svg>
  <h2 class="headline right" style="right:28px;top:218px;font-size:45px;line-height:1.2">What<br>if <em class="pink">RT Checked</em><br><em>in Every Day?</em></h2>
  <p class="sub right" style="right:28px;top:415px;font-size:27px">Stay Consistent with<br><span class="pink">RT in Your Pocket!</span></p>
</section>

<section class="tile col-r row-4">
  <svg class="art" viewBox="0 0 431 538">
    <path d="M0 0 L330 0 Q290 150 160 250 Q30 350 60 450 Q90 520 240 538 L0 538Z" fill="var(--rose)"/>
    <circle role="img" aria-label="Photo of the coach standing with a smiling client" cx="120" cy="85" r="170" fill="url(#photoWarm)"/>
  </svg>
  <h2 class="headline right" style="right:30px;top:178px;font-size:46px;line-height:1.2">The<br>Missing<br>Piece <span class="pink">Isn't</span><br><span class="pink">Another Diet</span></h2>
  <p class="sub right" style="right:30px;top:425px;font-size:27px">Stay Consistent with<br><span class="pink">RT in Your Pocket!</span></p>
</section>

<section class="tile col-l row-5">
  <svg class="art" viewBox="0 0 431 538">
    <rect width="431" height="538" fill="#fbe6ef"/>
    <circle cx="120" cy="70" r="190" fill="var(--blush)" opacity=".7"/>
    <circle cx="380" cy="170" r="200" fill="var(--blush)" opacity=".8"/>
    <circle cx="108" cy="540" r="206" fill="var(--hot)"/>
    <path role="img" aria-label="Photo of the coach in a black outfit, hand on hip" d="M330 290 Q350 275 365 295 L385 350 Q400 420 390 538 L310 538 Q300 440 300 370 Q305 320 330 290Z" fill="url(#photoTone)"/>
  </svg>
  <h2 class="headline" style="left:26px;top:28px;font-size:52px;line-height:1.1">Eat the food<br>you love.<br><span class="pink">Stay<br>accountable<br>every day.</span></h2>
  <p class="sub light" style="left:26px;top:380px;font-size:26px">Stay<br>Consistent<br>with RT in Your<br>Pocket!</p>
</section>

<section class="tile dark col-r row-5">
  <svg class="art" viewBox="0 0 431 538">
    <circle cx="399" cy="48" r="75" fill="var(--white)"/>
    <circle cx="243" cy="580" r="82" fill="var(--hot)"/>
    <circle cx="-10" cy="560" r="50" fill="var(--white)"/>
    <circle cx="340" cy="335" r="135" fill="var(--hot)"/>
    <circle role="img" aria-label="Photo of two women hugging and laughing" cx="335" cy="340" r="125" fill="url(#photoWarm)"/>
  </svg>
  <h2 class="headline light" style="left:24px;top:40px;font-size:48px;line-height:1.15"><em>One<br>Bad Meal</em><br>Doesn't<br>Mean<br><em>You<br>Failed</em></h2>
  <p class="sub light" style="left:24px;top:400px;font-size:24px">Stay Consistent<br>with <span class="hot">RT in Your</span><br><span class="hot">Pocket!</span></p>
</section>
</main>
</body>
</html>
```